Business Card for a Jewellery Brand

Business card for an upscale jewellery brand. Attached is the brand logo and icon and color board. I am looking for two card versions: one for the founder and one is generic. The card should be elegant and convey upscale and premium feel. I am open to both square and rectangle card shapes.

Industry/Entity Type

Jewelry

Contact Information for Business Card

Two cards: (1) Sunela Parvaniya (Founder) (2) General
(1) Sunela Parvaniya card should have Name: Sunela Parvaniya, Title: Founder Email id: sunela@quiremo.com.au. Phone no: +61452913307
(2) Generic card should have Email id: info@quiremo.com.au. Phone no: +61436207518

Requirements
Must have
• Workmark
• ICON
• Phone no
• Email ID
• ABN: 58219740312 (Note: ABN is Business number in Australia)
• Website: www.quiremo.com.au
• Instagram: quiremo_jewellery
• Facebook: @quiremojewellery
Nice to have
• Tagline

```html
<!DOCTYPE html>
<html lang="en">
<head>
<meta charset="utf-8">
<title>Quiremo Business Cards</title>
<link rel="stylesheet" href="https://fonts.googleapis.com/css2?family=Jost:wght@400;500&display=swap">
<style>
  :root {
    --backdrop: #2b2b2d;
    --card: #1a1a1b;
    --rose: #e9a196;
    --ink: #f1efee;
    --muted: #d9d6d4;
  }
  * { box-sizing: border-box; margin: 0; padding: 0; }
  html, body {
    width: 1200px;
    height: 900px;
    overflow: hidden;
    background: var(--backdrop);
    font-family: "Jost", "Futura", sans-serif;
  }
  .stage {
    width: 1200px;
    height: 900px;
    display: flex;
    flex-direction: column;
    align-items: center;
    justify-content: center;
    gap: 40px;
  }
  .card {
    position: relative;
    width: 640px;
    height: 366px;
    background: var(--card);
    box-shadow: 0 18px 40px rgba(0,0,0,0.45);
  }
  .card--front {
    display: flex;
    align-items: center;
    justify-content: center;
  }
  .wordmark {
    color: var(--rose);
    font-weight: 500;
    letter-spacing: 0.32em;
    text-transform: uppercase;
  }
  .card--front .wordmark { font-size: 52px; padding-left: 0.32em; }
  .card--back .wordmark {
    position: absolute;
    left: 44px;
    top: 40px;
    font-size: 38px;
  }
  .abn {
    position: absolute;
    right: 44px;
    top: 118px;
    font-size: 15px;
    letter-spacing: 0.1em;
    color: var(--ink);
  }
  .abn__label { color: var(--rose); }
  .person {
    position: absolute;
    right: 44px;
    top: 196px;
    text-align: right;
    text-transform: uppercase;
  }
  .person__name {
    color: var(--rose);
    font-size: 21px;
    font-weight: 500;
    letter-spacing: 0.08em;
  }
  .person__title {
    color: var(--ink);
    font-size: 17px;
    font-weight: 500;
    letter-spacing: 0.06em;
    margin-top: 2px;
  }
  .contacts {
    position: absolute;
    right: 44px;
    bottom: 36px;
    list-style: none;
    display: flex;
    flex-direction: column;
    gap: 6px;
    align-items: flex-end;
  }
  .contacts li {
    display: flex;
    align-items: center;
    gap: 14px;
    font-size: 16px;
    letter-spacing: 0.08em;
    color: var(--ink);
  }
  .contacts .accent { color: var(--rose); }
  .contacts svg { width: 16px; height: 16px; flex: none; }
  .socials {
    position: absolute;
    left: 44px;
    bottom: 52px;
    list-style: none;
    display: flex;
    flex-direction: column;
    gap: 6px;
  }
  .socials li {
    display: flex;
    align-items: center;
    gap: 16px;
    font-size: 16px;
    letter-spacing: 0.08em;
    color: var(--ink);
  }
  .socials__mark {
    width: 13px;
    height: 13px;
    background: var(--rose);
    border-radius: 2px;
  }
</style>
</head>
<body>
<main class="stage">
  <section class="card card--front" aria-label="Card front">
    <h1 class="wordmark">Quiremo</h1>
  </section>

  <section class="card card--back" aria-label="Card back">
    <p class="wordmark">Quiremo</p>
    <p class="abn"><span class="abn__label">ABN:</span> 58219740312</p>

    <div class="person">
      <p class="person__name">Sunela Parvaniya</p>
      <p class="person__title">Founder</p>
    </div>

    <ul class="contacts">
      <li>+61452913307
        <svg viewBox="0 0 16 16" aria-hidden="true"><rect x="4" y="1" width="8" height="14" rx="1.5" fill="none" stroke="#f1efee" stroke-width="1.4"/><line x1="7" y1="12.5" x2="9" y2="12.5" stroke="#f1efee" stroke-width="1.2"/></svg>
      </li>
      <li><span>www.<span class="accent">quiremo.com</span>.au</span>
        <svg viewBox="0 0 16 16" aria-hidden="true"><circle cx="7" cy="7" r="4.5" fill="none" stroke="#f1efee" stroke-width="1.8"/><line x1="10.3" y1="10.3" x2="14.5" y2="14.5" stroke="#f1efee" stroke-width="2"/></svg>
      </li>
      <li>sunela@quiremo.com.au
        <svg viewBox="0 0 16 16" aria-hidden="true"><rect x="1" y="3" width="14" height="10" fill="#e9a196"/><polyline points="1,3 8,9 15,3" fill="none" stroke="#1a1a1b" stroke-width="1.3"/></svg>
      </li>
    </ul>

    <ul class="socials">
      <li><span class="socials__mark"></span>quiremo_jewellery</li>
      <li><span class="socials__mark"></span>@quiremojewellery</li>
    </ul>
  </section>
</main>
</body>
</html>
```